Budget Brand Responsive Website

Flat vector style website needed for value based IT support company. looking for clean, illustration intensive based design. Current test site can be found at www.bright-mend.co.uk and holding page it www.brightmend.co.uk this will show text and services, please feel free to use placeholder text if you think we need alternative text in places. Emphasis should be on low cost support and services listed on the site, would be nice to see costs in bold images. important colors are the blue, orange and white, see holding page and attached image of an advert

It Company

```html
<!DOCTYPE html>
<html lang="en">
<head>
<meta charset="utf-8">
<title>Bright Mend – IT Services</title>
<link href="https://fonts.googleapis.com/css2?family=Montserrat:wght@400;600;700&family=Open+Sans:wght@400;600&display=swap" rel="stylesheet">
<style>
:root{
  --orange:#e07a2c;
  --orange-dark:#c9651c;
  --blue:#2e4b8c;
  --navy:#1a2946;
  --ink:#3b4250;
  --muted:#7c8492;
  --line:#d9dde3;
  --white:#ffffff;
  --paper:#f4f6f9;
}
*{box-sizing:border-box;margin:0;padding:0}
html,body{width:1200px;height:4324px;overflow:hidden}
body{font-family:"Open Sans",Arial,sans-serif;color:var(--ink);background:var(--white);position:relative}
h1,h2,h3,h4,.btn,.nav a,.logo{font-family:"Montserrat",Arial,sans-serif}
section,header,footer{position:absolute;left:0;width:1200px}

/* header */
.site-header{top:0;height:64px;background:var(--white);display:flex;align-items:center;justify-content:space-between;padding:0 60px;box-shadow:0 2px 6px rgba(0,0,0,.08);z-index:2}
.logo{display:flex;align-items:center;gap:10px;font-weight:700;font-size:26px;color:var(--blue);letter-spacing:1px}
.logo-mark{width:22px;height:22px;background:var(--orange)}
.nav{display:flex;gap:40px}
.nav a{font-size:14px;color:var(--ink);text-decoration:none}

/* hero */
.hero{top:64px;height:668px;overflow:hidden}
.hero-photo{position:absolute;inset:0;background:linear-gradient(100deg,#6f7c8e 0%,#b9c1cc 40%,#8c95a3 70%,#4e5868 100%)}
.hero-tint{position:absolute;inset:0;background:linear-gradient(90deg,rgba(26,41,70,.55),rgba(26,41,70,.1))}
.hero-copy{position:absolute;left:60px;top:210px;color:var(--white)}
.hero-copy h1{font-size:48px;font-weight:600;line-height:1.1;letter-spacing:.5px}
.hero-copy p{font-family:"Montserrat",sans-serif;color:var(--orange);font-size:20px;font-weight:600;line-height:1.2;margin-top:6px;width:560px}
.btn{display:inline-block;background:var(--orange);color:var(--white);font-size:14px;font-weight:600;text-transform:uppercase;letter-spacing:1px;border:0;text-align:center}
.hero-copy .btn{margin-top:22px;padding:14px 28px}

/* tied down */
.tied{top:732px;height:428px;background:var(--orange);color:var(--white);text-align:center;padding-top:100px}
.tied h2{font-size:44px;font-weight:400;letter-spacing:1px}
.tied .lead{width:1040px;margin:28px auto 0;font-size:14px;line-height:1.6}
.tied .ask{margin-top:26px;font-size:15px}
.tied .call{font-family:"Montserrat",sans-serif;font-size:28px;margin-top:12px}
.tied .call strong{font-weight:700}

/* services */
.services{top:1160px;height:1000px;background:var(--white)}
.section-title{text-align:center;font-size:42px;font-weight:600;color:var(--navy);letter-spacing:1px}
.section-sub{text-align:center;font-family:"Montserrat",sans-serif;color:var(--orange);font-size:20px;font-weight:600;letter-spacing:1px}
.services .section-title{margin-top:22px}
.service-card{position:absolute;width:320px;height:360px;background:var(--blue);color:var(--white);text-align:center;padding-top:28px}
.service-icon{width:96px;height:96px;border-radius:50%;background:var(--orange);margin:0 auto;display:flex;align-items:center;justify-content:center;border:4px solid rgba(255,255,255,.35)}
.service-card h3{font-size:20px;font-weight:700;margin-top:22px;letter-spacing:1px}
.service-card ul{list-style:none;margin-top:12px;font-size:13px;line-height:1.8;opacity:.9}
.service-card .btn{margin-top:24px;padding:10px 22px;font-size:12px}

/* technical support */
.tech{top:2160px;height:330px;overflow:hidden}
.tech-photo{position:absolute;inset:0;background:linear-gradient(90deg,#eef1f5 0%,#eef1f5 45%,#c9d0da 70%,#9aa4b2 100%)}
.tech-copy{position:absolute;left:60px;top:78px;width:560px}
.tech-copy h2{font-size:30px;font-weight:400;color:var(--blue);letter-spacing:1px}
.tech-copy p{font-size:13px;line-height:1.7;color:var(--muted);margin-top:16px}

/* pricing */
.pricing{top:2490px;height:810px;background:var(--white)}
.pricing .section-title{margin-top:22px}
.price-card{position:absolute;top:170px;width:245px;height:590px;background:var(--white);box-shadow:0 3px 12px rgba(0,0,0,.14);text-align:center}
.price-head{height:190px;background:var(--orange);color:var(--white);padding-top:26px}
.price-card.featured .price-head{background:var(--blue)}
.price-head p{font-size:12px;line-height:1.4;font-weight:600}
.price-head h3{font-size:34px;font-weight:700;margin-top:8px;letter-spacing:1px}
.price-icon{width:104px;height:104px;border-radius:50%;background:#4a4f58;border:6px solid var(--white);margin:-44px auto 0;display:flex;align-items:center;justify-content:center;position:relative}
.price-list{list-style:none;margin-top:18px;font-size:13px;color:var(--ink)}
.price-list li{padding:16px 0;border-bottom:1px solid var(--line);margin:0 22px}
.pick{display:block;margin:34px auto 0;width:170px;padding:12px 0;border:2px solid var(--orange);color:var(--orange);font-family:"Montserrat",sans-serif;font-size:14px}
.price-card.featured .pick{border-color:var(--blue);color:var(--blue)}

/* expectations */
.exceed{top:3300px;height:280px;overflow:hidden}
.exceed-photo{position:absolute;inset:0;background:linear-gradient(90deg,#172440,#243a66 55%,#1a2946)}
.gauge{position:absolute;left:110px;top:58px}
.exceed-copy{position:absolute;left:340px;top:74px;width:780px}
.exceed-copy h2{font-size:34px;font-weight:400;color:var(--orange);letter-spacing:1px}
.exceed-copy p{color:#cdd5e3;font-size:13px;line-height:1.7;margin-top:14px}

/* contact */
.contact{top:3580px;height:500px;background:var(--white)}
.contact h2{position:absolute;top:70px;left:0;width:1200px;text-align:center;font-size:26px;font-weight:400;letter-spacing:1px;color:var(--navy)}
.contact h2::before,.contact h2::after{content:"";position:absolute;top:16px;width:230px;height:1px;background:var(--line)}
.contact h2::before{left:60px}
.contact h2::after{right:60px}
.field{position:absolute;height:44px;border:1px solid var(--line);font-size:13px;color:#9aa1ad;padding:12px 14px}
.field.message{height:110px}
.contact .btn{position:absolute;left:450px;top:346px;width:300px;padding:14px 0;font-size:15px}

/* footer */
.site-footer{top:4080px;height:244px;background:linear-gradient(180deg,#eef1f5,#dfe4ea)}
.office{position:absolute;top:48px}
.office h4{font-size:22px;font-weight:600;color:var(--navy)}
.office p{font-size:13px;line-height:1.55;color:var(--ink);margin-top:4px}
.footer-bar{position:absolute;left:0;bottom:0;width:1200px;height:56px;border-top:1px solid #c8ced7;display:flex;align-items:center;justify-content:space-between;padding:0 60px;font-size:12px;color:var(--muted)}
.social{display:flex;gap:14px}
.social span{width:28px;height:28px;border-radius:50%;background:var(--orange)}
</style>
</head>
<body>

<header class="site-header">
  <div class="logo"><span class="logo-mark"></span>BRIGHT MEND</div>
  <nav class="nav"><a href="#">Home</a><a href="#">Support</a><a href="#">Services</a><a href="#">About</a><a href="#">Contact</a></nav>
</header>

<section class="hero">
  <div class="hero-photo" role="img" aria-label="Photograph of two business people working together at a laptop in a bright office"></div>
  <div class="hero-tint"></div>
  <div class="hero-copy">
    <h1>IT SERVICES THE BRIGHT WAY</h1>
    <p>WE HELP OUR CLIENTS INCREASE PRODUCTIVITY WHILST REDUCING COST</p>
    <span class="btn">Learn More</span>
  </div>
</section>

<section class="tied">
  <h2>DON'T GET TIED DOWN!</h2>
  <p class="lead">We don't believe any local business should pay for IT support they don't need. You shouldn't be stuck with a long contract or locked into costly technology. If you're not happy with the service you're getting from your provider, you should be free to walk away. As a local business ourselves, we treat every client the way we would want to be treated.</p>
  <p class="ask">Want to learn how other businesses are profiting from our IT?</p>
  <p class="call">Call us today on <strong>01632 960 440</strong></p>
</section>

<section class="services">
  <h2 class="section-title">SERVICES</h2>
  <p class="section-sub">TAILORED FOR YOU</p>

  <div class="service-card" style="left:80px;top:150px">
    <div class="service-icon"><svg width="54" height="54" viewBox="0 0 54 54" fill="none" stroke="#fff" stroke-width="4"><circle cx="27" cy="27" r="22"/><circle cx="27" cy="27" r="9"/><path d="M11 11l10 10M43 11L33 21M11 43l10-10M43 43L33 33"/></svg></div>
    <h3>SUPPORT</h3>
    <ul><li>Unlimited Remote Support</li><li>Monitoring, Auditing &amp; more</li><li>All from £6.00 a month</li></ul>
    <span class="btn">Read More</span>
  </div>
  <div class="service-card" style="left:440px;top:150px">
    <div class="service-icon"><svg width="56" height="40" viewBox="0 0 56 40" fill="none" stroke="#fff" stroke-width="4" stroke-linecap="round"><path d="M4 20h4M12 12v16M20 4v32M28 10v20M36 2v36M44 12v16M52 20h0"/></svg></div>
    <h3>VOICE</h3>
    <ul><li>VoIP Telephone Systems</li><li>Telephone Lines</li><li>SIP Trunking &amp; more</li></ul>
    <span class="btn">Read More</span>
  </div>
  <div class="service-card" style="left:800px;top:150px">
    <div class="service-icon"><svg width="54" height="54" viewBox="0 0 54 54" fill="none" stroke="#fff" stroke-width="3.5"><circle cx="27" cy="27" r="22"/><ellipse cx="27" cy="27" rx="10" ry="22"/><path d="M5 27h44M9 16h36M9 38h36"/></svg></div>
    <h3>INTERNET</h3>
    <ul><li>Business Broadband</li><li>Leased Lines</li><li>Fibre Broadband</li></ul>
    <span class="btn">Read More</span>
  </div>
  <div class="service-card" style="left:80px;top:570px">
    <div class="service-icon"><svg width="44" height="54" viewBox="0 0 44 54" fill="none" stroke="#fff" stroke-width="4"><path d="M11 24V16a11 11 0 0 1 22 0v8"/><rect x="4" y="24" width="36" height="26" rx="3" fill="#fff"/></svg></div>
    <h3>SECURITY</h3>
    <ul><li>Encryption</li><li>Antivirus &amp; Anti-Malware</li><li>Patch Management Solutions</li></ul>
    <span class="btn">Read More</span>
  </div>
  <div class="service-card" style="left:440px;top:570px">
    <div class="service-icon"><svg width="58" height="46" viewBox="0 0 58 46" fill="#fff"><path d="M14 40a12 12 0 0 1-1-24 16 16 0 0 1 31 2 11 11 0 0 1 0 22z"/><path d="M29 36V20M22 26l7-7 7 7" stroke="#e07a2c" stroke-width="4" fill="none"/></svg></div>
    <h3>HOSTING</h3>
    <ul><li>Hosted Email</li><li>Cloud Office Suite</li><li>Email Protection</li></ul>
    <span class="btn">Read More</span>
  </div>
  <div class="service-card" style="left:800px;top:570px">
    <div class="service-icon"><svg width="58" height="46" viewBox="0 0 58 46" fill="#fff"><path d="M14 40a12 12 0 0 1-1-24 16 16 0 0 1 31 2 11 11 0 0 1 0 22z"/></svg></div>
    <h3>CLOUD</h3>
    <ul><li>Backup and DR</li><li>Virtual Desktop</li><li>Virtual Private Servers</li></ul>
    <span class="btn">Read More</span>
  </div>
</section>

<section class="tech">
  <div class="tech-photo" role="img" aria-label="Soft background photograph of an engineer working at a laptop"></div>
  <div class="tech-copy">
    <h2>TECHNICAL SUPPORT</h2>
    <p>Our highly skilled and certified engineers are on hand to support your business and utilise advanced technologies to proactively monitor and maintain your systems 24/7 and prevent issues before they occur.</p>
    <p>The level of service is offered to all our clients; we believe in providing you a service to suit your business needs.</p>
  </div>
</section>

<section class="pricing">
  <h2 class="section-title">PRICING</h2>
  <p class="section-sub">FOR OUR MOST POPULAR SERVICES</p>

  <div class="price-card" style="left:100px">
    <div class="price-head"><p>Unlimited Monthly<br>Remote Support</p><h3>SUPPORT</h3></div>
    <div class="price-icon"><svg width="54" height="54" viewBox="0 0 54 54" fill="none" stroke="#fff" stroke-width="4"><circle cx="27" cy="27" r="22"/><circle cx="27" cy="27" r="9"/><path d="M11 11l10 10M43 11L33 21M11 43l10-10M43 43L33 33"/></svg></div>
    <ul class="price-list"><li>Workstations £6.00</li><li>Antivirus from £3.00</li><li>Servers £49.00</li></ul>
    <span class="pick">Pick It</span>
  </div>
  <div class="price-card" style="left:360px">
    <div class="price-head"><p>Super Fast and<br>Low Charges</p><h3>VOICE</h3></div>
    <div class="price-icon"><svg width="56" height="40" viewBox="0 0 56 40" fill="none" stroke="#fff" stroke-width="4" stroke-linecap="round"><path d="M4 20h4M12 12v16M20 4v32M28 10v20M36 2v36M44 12v16M52 20h0"/></svg></div>
    <ul class="price-list"><li>PBX from £40.00</li><li>Line rental from £11.00</li><li>Phone numbers from £5.00</li></ul>
    <span class="pick">Pick It</span>
  </div>
  <div class="price-card featured" style="left:620px">
    <div class="price-head"><p>Flexible and Secure<br>Hosting</p><h3>HOSTING</h3></div>
    <div class="price-icon"><svg width="58" height="46" viewBox="0 0 58 46" fill="#fff"><path d="M14 40a12 12 0 0 1-1-24 16 16 0 0 1 31 2 11 11 0 0 1 0 22z"/><path d="M29 36V20M22 26l7-7 7 7" stroke="#4a4f58" stroke-width="4" fill="none"/></svg></div>
    <ul class="price-list"><li>Email Archiving from £3.00</li><li>Email Protection from £1.00</li><li>Cloud Office from £3.10</li></ul>
    <span class="pick">Pick It</span>
  </div>
  <div class="price-card" style="left:880px">
    <div class="price-head"><p>Reduce Costs &amp;<br>Increase Performance</p><h3>CLOUD</h3></div>
    <div class="price-icon"><svg width="58" height="46" viewBox="0 0 58 46" fill="#fff"><path d="M14 40a12 12 0 0 1-1-24 16 16 0 0 1 31 2 11 11 0 0 1 0 22z"/></svg></div>
    <ul class="price-list"><li>Online Backup</li><li>Private Cloud Servers</li><li>Virtual Desktop</li></ul>
    <span class="pick">Pick It</span>
  </div>
</section>

<section class="exceed">
  <div class="exceed-photo" role="img" aria-label="Dark blue tinted photograph of a busy office team"></div>
  <svg class="gauge" width="164" height="164" viewBox="0 0 164 164">
    <circle cx="82" cy="82" r="74" fill="none" stroke="rgba(255,255,255,.2)" stroke-width="6"/>
    <circle cx="82" cy="82" r="74" fill="none" stroke="#e07a2c" stroke-width="6" stroke-dasharray="418.5 465" transform="rotate(-90 82 82)"/>
    <text x="82" y="94" text-anchor="middle" fill="#fff" font-family="Montserrat, sans-serif" font-size="34">90%</text>
  </svg>
  <div class="exceed-copy">
    <h2>WE EXCEED EXPECTATIONS</h2>
    <p>Unlike traditional IT support companies and other managed service providers, we do not just meet our targets, we beat them. Our commitment is that your systems are looked after by people who care about your success, and our responsiveness is directly measured.</p>
  </div>
</section>

<section class="contact">
  <h2>PLEASE DO NOT HESITATE TO CONTACT US</h2>
  <div class="field" style="left:120px;top:170px;width:300px">Full Name</div>
  <div class="field" style="left:450px;top:170px;width:300px">Email</div>
  <div class="field" style="left:780px;top:170px;width:300px">Subject</div>
  <div class="field message" style="left:120px;top:230px;width:960px">Message</div>
  <span class="btn">Submit</span>
</section>

<footer class="site-footer">
  <div class="office" style="left:60px"><h4>EAST OFFICE</h4><p>Eastbridge-on-Sea<br>east@brightmend.co.uk</p></div>
  <div class="office" style="left:340px"><h4>NORTH OFFICE</h4><p>Millford<br>north@brightmend.co.uk</p></div>
  <div class="office" style="left:640px"><h4>SUPPORT</h4><p>support@brightmend.co.uk<br>+44 01632 960 440</p></div>
  <div class="office" style="left:920px"><h4>SALES</h4><p>sales@brightmend.co.uk<br>+44 01632 960 440</p></div>
  <div class="footer-bar">
    <span>© 2016 Copyright. All Rights Reserved | Privacy Policy</span>
    <div class="social"><span></span><span></span><span></span><span></span></div>
  </div>
</footer>

</body>
</html>
```